Business card for Luxury Portable Restroom Trailer company

We are a Luxury Portable Restroom Trailer Company Called FALCRIDGE HIRES. Based in Orange County California. We provide portable restroom trailers for events, such as, Weddings, Concerts, Charity events, Sporting events, Tournaments, Corporate events, ect. We rent and Sell the Luxury restrooms. Our colors are white, grey, and Orange. As you will see in the logo we uploaded.
There are 2 people in the company so the names and titles will change for the 3 people but card will remain the same. Here is the information for each Person: Dwight Penner CFO 555 318-0476
next Person: Leon Marchetti VP 555 318-0476
Next Person: Owen Marchetti CEO 555 318-0476
Information to include on the card: Luxury Restroom Trailers Rental and Sales. Weddings, Concerts, Charity, Sporting and Corp. Events.

```html
<!DOCTYPE html>
<html lang="en">
<head>
<meta charset="utf-8">
<title>Falcridge Hires – Business Card</title>
<link rel="stylesheet" href="https://fonts.googleapis.com/css2?family=Archivo:wght@400;600;700&display=swap">
<style>
  :root {
    --backdrop: #3a3a3a;
    --card: #2b2b2c;
    --card-edge: #232324;
    --accent: #f26a1b;
    --ink-light: #f2f2f2;
    --ink-muted: #bdbdbd;
    --logo-grey: #7d7d80;
    --deco-dark: #262627;
    --deco-light: #4a4a4c;
  }
  * { box-sizing: border-box; margin: 0; padding: 0; }
  html, body { width: 1200px; height: 689px; overflow: hidden; }
  body {
    background: var(--backdrop);
    font-family: "Archivo", Arial, sans-serif;
    position: relative;
  }
  .card {
    position: absolute;
    top: 195px;
    width: 525px;
    height: 300px;
    background: var(--card);
    border-radius: 18px;
    border-bottom: 3px solid var(--accent);
    overflow: hidden;
  }
  .card--front { left: 50px; }
  .card--back { left: 625px; }

  /* Front */
  .brand {
    position: absolute;
    top: 92px;
    left: 0;
    right: 0;
    display: flex;
    justify-content: center;
    align-items: center;
    gap: 12px;
  }
  .brand__mark {
    width: 26px;
    height: 26px;
    background: var(--logo-grey);
  }
  .brand__name {
    font-weight: 700;
    font-size: 34px;
    letter-spacing: 2px;
    color: var(--logo-grey);
  }
  .services {
    position: absolute;
    top: 196px;
    left: 0;
    right: 0;
    text-align: center;
    color: var(--ink-light);
    font-size: 14px;
    line-height: 1.35;
  }

  /* Back */
  .back-frame {
    position: absolute;
    inset: 10px;
    border: 2px solid var(--accent);
    border-radius: 14px;
  }
  .decor {
    position: absolute;
    top: 0;
    right: 0;
    width: 330px;
    height: 210px;
    border-bottom-left-radius: 100% 90%;
    background: radial-gradient(ellipse at 70% 30%, var(--deco-light), var(--deco-dark) 75%);
  }
  .person {
    position: absolute;
    left: 40px;
    bottom: 34px;
  }
  .person__name {
    font-weight: 700;
    font-size: 22px;
    color: var(--accent);
    text-transform: uppercase;
    letter-spacing: 0.5px;
  }
  .person__title {
    font-size: 13px;
    color: var(--ink-muted);
    margin-bottom: 12px;
  }
  .contact {
    list-style: none;
    font-size: 13px;
    color: var(--ink-light);
  }
  .contact li {
    display: flex;
    align-items: center;
    gap: 10px;
    line-height: 1.5;
  }
  .contact svg { width: 12px; height: 12px; fill: var(--accent); flex: none; }
</style>
</head>
<body>

  <section class="card card--front">
    <div class="brand">
      <span class="brand__mark"></span>
      <span class="brand__name">FALCRIDGE HIRES</span>
    </div>
    <p class="services">
      Luxury Restroom Trailers Rental and Sales.<br>
      Weddings • Concerts • Charity • Sporting and Corp. Events
    </p>
  </section>

  <section class="card card--back">
    <div class="decor" role="img" aria-label="Large faint brand illustration in dark grey tones"></div>
    <div class="back-frame"></div>
    <div class="person">
      <h1 class="person__name">Dwight Penner</h1>
      <p class="person__title">CFO</p>
      <ul class="contact">
        <li>
          <svg viewBox="0 0 24 24"><path d="M6.6 10.8a15 15 0 0 0 6.6 6.6l2.2-2.2a1 1 0 0 1 1-.25 11.4 11.4 0 0 0 3.6.57 1 1 0 0 1 1 1V20a1 1 0 0 1-1 1A17 17 0 0 1 3 4a1 1 0 0 1 1-1h3.5a1 1 0 0 1 1 1c0 1.25.2 2.45.57 3.6a1 1 0 0 1-.25 1z"/></svg>
          555 318-0476
        </li>
        <li>
          <svg viewBox="0 0 24 24"><path d="M2 5h20v14H2z M4 7v.5l8 5 8-5V7l-8 5z" fill-rule="evenodd"/></svg>
          info@falcridgehires.com
        </li>
        <li>
          <svg viewBox="0 0 24 24"><circle cx="12" cy="12" r="10"/></svg>
          www.falcridgehires.com
        </li>
      </ul>
    </div>
  </section>

</body>
</html>
```